Need App for Impact Related Events

My app is to help with internal events. When you enter the prompted event code the next screen shows you everyone currently at the event. It will give you the ability to Start a conversation with someone you met at that event, or signal it is your turn to send a message. The next screen is a message thread with that person. I am looking for a design that incorporates the colors and ‘feel good’ emotion of our logo. I have pieced together a pretty good interpretation of what I’m looking for in the attached mockup by slicing and dicing designs. I also attached our logo mascot.Screens (see attached mockups)

Note 1: I do not like the picture on the screen used in screen one because it makes it seem like a dating app. I attached an alternative photo that can be used or present different ideas.

Note 2: On the login/signup screen (screen 2) I need an additional first and last name for login, you can try to fit this on one login screen or present a two step signup screen where that is presented in the second screen.

READ MOCKUP GUIDELINES UNDER Must Haves

Target Market(s)

People attending internal social impact events

Industry/Entity Type

Charity

Font styles to use
Sans Serif

Colors
86cfc6

Requirements
Must have
• Follow the screen mockups attached to project
• PLEASE READ
• I have provided a relatively close design of what I’m looking for in the mockups. Some screens need to be followed more closely to my design mockup than other. I have listed a guide below how how closely you should follow my mockup design exactly. Overall I would like to see some ideas of incorporating a few accent colors so it doesn’t appear SO Blue. I also attached some app inspiration designs I found from around the web
• Screen Mockup Guideline Follow %
• Screen 1: 65% - mostly on target, would like to see ways to make it not SO Blue and possibly creative places to add some explainer text describing the app
• Screen 2: 50% - general design idea is here, but more open
• Screen 3: 35% - a lot more room for design influence
• Screen 4: 70% - mostly on target, a little room for design influence/color scheme ideas
• Screen 5-6: 25% - a lot of room for design change/ideas/influence
• Screen 7-8: 80% - already very close to what I need, maybe open to slight sizing and color scheme ideas
• Screen 9: 15% - the most open for influence, only the general functionality of the screen is communicated here
Nice to have
• Please Read Mockup Guideline above. In large part I am looking for something to use some nice accent colors so it is not overwhelmingly blue and bring the whole design into a seamless style.
Should not have

```html
<!DOCTYPE html>
<html lang="en">
<head>
<meta charset="utf-8">
<title>Events – Enter the Code</title>
<link href="https://fonts.googleapis.com/css2?family=Lato:wght@400;700;900&family=Roboto:wght@400;500&display=swap" rel="stylesheet">
<style>
  :root {
    --page-bg: #c7a3ea;
    --page-bg-top: #c39ce8;
    --title: #7a4bb0;
    --ghost-line: #d5b8f0;
    --card-body: #d8bde9;
    --card-title: #9565b4;
    --card-meta: #a783bf;
    --photo-a: #d07ad9;
    --photo-b: #b95bc9;
    --photo-c: #c98be0;
    --modal-bg: #ffffff;
    --modal-title: #2c2a36;
    --field-border: #e2e2e6;
    --placeholder: #7a7a80;
    --body-text: #62606a;
    --btn-start: #9a57ec;
    --btn-end: #d996bd;
    --btn-text: #ffffff;
    --kbd-bg: #f2f2f4;
    --kbd-divider: #d8d8dc;
    --key-text: #2e2e32;
    --key-hint: #5f5f64;
    --space-bar: #dcdcde;
    --enter-blue: #3a83ee;
  }
  * { box-sizing: border-box; margin: 0; padding: 0; }
  html, body { width: 675px; height: 1200px; overflow: hidden; }
  body {
    position: relative;
    font-family: "Lato", sans-serif;
    background: linear-gradient(180deg, var(--page-bg-top), var(--page-bg));
  }

  .app-title {
    position: absolute; left: 30px; top: 38px;
    font-size: 48px; font-weight: 900; color: var(--title);
  }
  .profile-avatar {
    position: absolute; left: 577px; top: 34px;
    width: 68px; height: 68px; border-radius: 50%;
    background: radial-gradient(circle at 45% 40%, #a6849e, #6f4f69);
  }
  .search-ghost {
    position: absolute; left: 56px; top: 141px; width: 563px; height: 70px;
    border: 2px solid var(--ghost-line); border-radius: 8px;
  }

  .event-card {
    position: absolute; left: 30px; top: 337px; width: 615px; height: 500px;
    border-radius: 10px; overflow: hidden; background: var(--card-body);
  }
  .event-photo {
    height: 300px;
    background: radial-gradient(circle at 15% 25%, var(--photo-c), transparent 45%),
                radial-gradient(circle at 85% 60%, var(--photo-a), transparent 50%),
                linear-gradient(135deg, var(--photo-a), var(--photo-b));
  }
  .event-name {
    position: absolute; left: 18px; top: 322px;
    font-size: 37px; font-weight: 700; color: var(--card-title);
  }
  .event-date {
    position: absolute; left: 18px; top: 385px;
    font-size: 24px; color: var(--card-meta); word-spacing: 6px;
  }
  .attendees { position: absolute; left: 337px; top: 382px; display: flex; gap: 10px; }
  .attendees span {
    width: 62px; height: 62px; border-radius: 50%;
    background: linear-gradient(135deg, #b99ab8, #8d6f8e);
  }
  .attendees span:last-child { background: linear-gradient(135deg, #b86ad8, #9a4cc4); }

  .code-modal {
    position: absolute; left: 88px; top: 163px; width: 501px; height: 488px;
    background: var(--modal-bg); border-radius: 10px;
    box-shadow: 0 6px 24px rgba(90, 40, 130, 0.18);
    text-align: center;
  }
  .modal-title {
    margin-top: 30px; font-size: 37px; font-weight: 700; color: var(--modal-title);
  }
  .code-field {
    position: absolute; left: 25px; top: 111px; width: 451px; height: 75px;
    border: 2px solid var(--field-border); border-radius: 12px;
    font-size: 26px; color: var(--placeholder);
    text-align: left; padding-left: 27px; line-height: 71px;
  }
  .modal-hint {
    position: absolute; left: 20px; right: 20px; top: 228px;
    font-size: 24px; line-height: 35px; color: var(--body-text);
  }
  .enter-button {
    position: absolute; left: 100px; top: 364px; width: 300px; height: 75px;
    border-radius: 8px;
    background: linear-gradient(90deg, var(--btn-start), var(--btn-end));
    box-shadow: 0 4px 12px rgba(154, 87, 236, 0.3);
    color: var(--btn-text); font-size: 22px; font-weight: 900;
    letter-spacing: 2px; line-height: 75px;
  }

  .keyboard {
    position: absolute; left: 0; top: 737px; width: 675px; height: 463px;
    background: var(--kbd-bg);
    font-family: "Roboto", sans-serif; color: var(--key-text);
  }
  .suggestions {
    height: 82px; display: flex; align-items: center;
    border-bottom: 1px solid #e4e4e8;
  }
  .suggestion {
    flex: 1; text-align: center; font-size: 30px; color: #3c3c40;
  }
  .suggestion + .suggestion { border-left: 2px solid var(--kbd-divider); }
  .suggestions .mic { width: 90px; display: flex; justify-content: center; }
  .key-row { position: absolute; left: 0; display: flex; }
  .key {
    position: relative; width: 67.5px; height: 90px;
    font-size: 36px; text-align: center; line-height: 90px;
  }
  .key sup {
    position: absolute; top: 2px; right: 12px; line-height: 1;
    font-size: 19px; color: var(--key-hint);
  }
  .row-1 { top: 86px; }
  .row-2 { top: 184px; left: 34px; }
  .row-3 { top: 279px; left: 101px; }
  .side-key {
    position: absolute; display: flex; align-items: center; justify-content: center;
    width: 90px; height: 90px;
  }
  .bottom-row { position: absolute; top: 366px; left: 0; width: 675px; height: 90px; }
  .bottom-row .label { font-size: 25px; }
  .space-bar {
    position: absolute; left: 253px; top: 26px; width: 235px; height: 44px;
    background: var(--space-bar); border-radius: 4px;
  }
</style>
</head>
<body>
  <h1 class="app-title">Events</h1>
  <div class="profile-avatar" role="img" aria-label="Profile photo of the signed-in user"></div>
  <div class="search-ghost"></div>

  <article class="event-card">
    <div class="event-photo" role="img" aria-label="Event photo with pink party balloons"></div>
    <h2 class="event-name">Maya's Party</h2>
    <p class="event-date">22 . Sep . 2018</p>
    <div class="attendees" role="img" aria-label="Attendee profile photos">
      <span></span><span></span><span></span><span></span>
    </div>
  </article>

  <section class="code-modal">
    <h2 class="modal-title">Enter the Code</h2>
    <div class="code-field">Event Code</div>
    <p class="modal-hint">Please enter the Event code that you received by your friend or family</p>
    <div class="enter-button">ENTER</div>
  </section>

  <div class="keyboard">
    <div class="suggestions">
      <div class="suggestion">Hi</div>
      <div class="suggestion">Hello</div>
      <div class="suggestion">Howdy</div>
      <div class="mic">
        <svg width="22" height="34" viewBox="0 0 22 34" fill="#5f5f64"><rect x="6" y="0" width="10" height="20" rx="5"/><path d="M2 15a9 9 0 0 0 18 0" fill="none" stroke="#5f5f64" stroke-width="2.5"/><rect x="9.7" y="24" width="2.6" height="8"/></svg>
      </div>
    </div>

    <div class="key-row row-1">
      <div class="key">q<sup>1</sup></div><div class="key">w<sup>2</sup></div><div class="key">e<sup>3</sup></div><div class="key">r<sup>4</sup></div><div class="key">t<sup>5</sup></div><div class="key">y<sup>6</sup></div><div class="key">u<sup>7</sup></div><div class="key">i<sup>8</sup></div><div class="key">o<sup>9</sup></div><div class="key">p<sup>0</sup></div>
    </div>
    <div class="key-row row-2">
      <div class="key">a</div><div class="key">s</div><div class="key">d</div><div class="key">f</div><div class="key">g</div><div class="key">h</div><div class="key">j</div><div class="key">k</div><div class="key">l</div>
    </div>
    <div class="side-key" style="left:6px;top:279px;">
      <svg width="36" height="38" viewBox="0 0 36 38" fill="#3a3a3e"><path d="M18 2 2 20h9v8h14v-8h9z"/><rect x="11" y="32" width="14" height="4"/></svg>
    </div>
    <div class="key-row row-3">
      <div class="key">z</div><div class="key">x</div><div class="key">c</div><div class="key">v</div><div class="key">b</div><div class="key">n</div><div class="key">m</div>
    </div>
    <div class="side-key" style="left:576px;top:279px;">
      <svg width="40" height="28" viewBox="0 0 40 28" fill="#3a3a3e"><path d="M12 0h26a2 2 0 0 1 2 2v24a2 2 0 0 1-2 2H12L0 14z"/><path d="M19 8l12 12M31 8 19 20" stroke="#f2f2f4" stroke-width="3"/></svg>
    </div>

    <div class="bottom-row">
      <div class="side-key label" style="left:6px;top:0;">?123</div>
      <div class="side-key label" style="left:88px;top:0;">,</div>
      <div class="side-key" style="left:156px;top:0;">
        <svg width="32" height="32" viewBox="0 0 32 32"><circle cx="16" cy="16" r="13" fill="none" stroke="#5f5f64" stroke-width="2.5"/></svg>
      </div>
      <div class="space-bar"></div>
      <div class="side-key label" style="left:494px;top:0;">.</div>
      <div class="side-key" style="left:576px;top:0;">
        <svg width="56" height="56" viewBox="0 0 56 56"><circle cx="28" cy="28" r="28" fill="var(--enter-blue)"/><path d="M38 18v12H19m6-7-7 7 7 7" fill="none" stroke="#fff" stroke-width="3.5" stroke-linecap="round" stroke-linejoin="round"/></svg>
      </div>
    </div>
  </div>
</body>
</html>
```